KorvaNest - Home Income and Business Resources Platform

I am looking for a website template for a multi-purposed website. This website will feature:

1.) Website Directory with Ratings & comments on listings
2.) Company Blog
3.) Homepage with Content (see files for homepage mock)

I would like the Design to have a default width 1170px (wider then normal)

Of course I am looking for Pages for Listings to be designed.

Great looking BLOG Layout: http://journal.plimworks.example/html/blog.html

I would like 4 Versions of a Website Directory Listing "Box"
1.) Basic Listing Box
2.) Sponsored Listing Box
3.) Recommended Listing Box
4.) Stay Away From Listing Box

Information on the Listing Page (Like on a Category Page)
Site Name, Site URL, Website Image, # of Views, Rating and # of Comments

Information on the Listing Details Page:
Same as ABOVE + About website Description, Vornic Score, Category Information

Decent looking examples is here: https://samples.trevolin.example/directory/computers/ and http://www.zqrankhub.example/.

I will include some sketches and screenshots of things I like/looking for. As designers,you have creative freedom and are encouraged to show this. This is Phase one of this project and winning designer is guaranteed to have future work for this project.

Target Market(s)

Directory, business, websites

Industry/Entity Type

Business

Coding

Coded - Design and coding required

Number of Pages Required

5+ page

Font styles to use
Sans Serif

Colors

Designer to choose colors to be used in the design.

Requirements
Must have
• Professional yet clean look. The use of Icons & images
• Unique Look
Should not have
• Any exact copies of any examples I provided

```html
<!DOCTYPE html>
<html lang="en">
<head>
<meta charset="utf-8">
<title>KorvaNest – Home Income and Business Resources</title>
<link href="https://fonts.googleapis.com/css2?family=Mulish:wght@400;600&family=Open+Sans:wght@400;600&display=swap" rel="stylesheet">
<style>
:root{
  --ink:#0d2236;
  --nav:#555a60;
  --page:#f1f1f1;
  --white:#ffffff;
  --line:#d6d6d6;
  --blue:#2a9be0;
  --blue-dark:#1f86d0;
  --orange:#f39a1e;
  --green:#7fb43a;
  --text:#6b6f74;
  --sponsor-link:#2a9be0;
  --logo-grey:#8e9195;
  --footer:#0b2a40;
  --footer-text:#c8d2da;
}
*{box-sizing:border-box;margin:0;padding:0}
html,body{width:1200px;height:1075px;overflow:hidden}
body{background:var(--page);font-family:"Open Sans",sans-serif;position:relative;color:var(--text)}
.site-header{position:absolute;left:0;top:0;width:1200px;height:109px;background:var(--white);box-shadow:0 1px 3px rgba(0,0,0,.06)}
.brand{position:absolute;left:116px;top:40px;font-family:"Mulish",sans-serif;font-size:34px;font-weight:400;color:var(--ink);line-height:1}
.main-nav{position:absolute;top:48px;left:0;font-family:"Mulish",sans-serif;font-size:18px;color:var(--nav)}
.main-nav a{position:absolute;white-space:nowrap;color:inherit;text-decoration:none}
.main-nav a.active{color:#111;font-weight:600}
.hero{position:absolute;left:117px;top:153px;width:701px;height:329px;
  background:linear-gradient(120deg,#2d8fd8 0%,#42a6ec 45%,#2b8bd6 100%)}
.hero-frame{position:absolute;left:13px;top:12px;right:13px;bottom:12px;border:1px solid rgba(255,255,255,.85)}
.hero h1{position:absolute;left:54px;top:57px;font-family:"Mulish",sans-serif;font-weight:400;font-size:31px;color:var(--white);white-space:nowrap}
.hero p{position:absolute;left:54px;width:630px;font-family:"Mulish",sans-serif;font-size:14.6px;line-height:29px;color:var(--white)}
.card{position:absolute;top:501px;width:223px;height:433px;background:var(--white);border:1px solid var(--line);padding:21px 22px 0 30px}
.card h2{font-family:"Mulish",sans-serif;font-weight:400;font-size:17px;color:#1d2124;white-space:nowrap;padding-bottom:11px;margin-left:0;border-bottom:2px solid}
.card .body{margin-top:13px;font-size:12.3px;line-height:18.1px;color:var(--text)}
.card .icon{float:left;width:74px;height:72px;margin-top:2px}
.card-resources h2{border-color:var(--blue)}
.card-ads h2{border-color:var(--orange)}
.card-earn h2{border-color:var(--green)}
.sidebar{position:absolute;left:834px;top:153px;width:248px;height:781px;background:var(--white);border:1px solid var(--line)}
.sidebar h2{position:absolute;left:31px;top:20px;font-family:"Mulish",sans-serif;font-weight:400;font-size:21px;color:#666a6f;white-space:nowrap}
.sponsor{position:absolute;left:31px}
.sponsor-name{font-family:"Mulish",sans-serif;font-weight:600;font-size:28px;color:var(--logo-grey);line-height:1}
.sponsor a{display:block;margin-top:8px;font-family:"Mulish",sans-serif;font-size:13.5px;color:var(--sponsor-link);text-decoration:none;white-space:nowrap}
.ad{position:absolute;left:20px;width:207px;height:207px}
.ad-energy{top:338px;background:linear-gradient(90deg,#4a4a3c 0%,#7c6d4a 45%,#3b86c8 55%,#8fc0e6 100%);}
.ad-energy::after{content:"";position:absolute;left:0;right:0;bottom:0;height:40px;background:#e2442a}
.ad-deli{top:557px;background:linear-gradient(180deg,#e8382a 0%,#e8382a 55%,#7a5a44 56%,#5e4532 100%)}
.site-footer{position:absolute;left:0;top:989px;width:1200px;height:86px;background:var(--footer)}
.site-footer small{position:absolute;left:133px;top:29px;font-family:"Mulish",sans-serif;font-size:13.4px;color:var(--footer-text)}
.social{position:absolute;left:945px;top:21px;display:flex;gap:4px}
.social span{width:32px;height:32px;border:1.5px solid var(--white);border-radius:50%}
</style>
</head>
<body>
<header class="site-header">
  <div class="brand">KorvaNest</div>
  <nav class="main-nav">
    <a class="active" style="left:398px" href="#">Home</a>
    <a style="left:497px" href="#">About Us</a>
    <a style="left:625px" href="#">Services</a>
    <a style="left:747px" href="#">Resources</a>
    <a style="left:884px" href="#">Sponsors</a>
    <a style="left:1014px" href="#">Contact</a>
  </nav>
</header>

<section class="hero" role="img" aria-label="Business team meeting photo under a blue overlay">
  <div class="hero-frame"></div>
  <h1>About KorvaNest</h1>
  <p style="top:119px">Praesent elementum elit at tellus nec ultricies sit amet porttitor mattis enim In massa libero interdum nec interdum vel blandit sed nulla In ullamcorper est eget tempor cursus neque mi consectetuer mi a ultricies massa est sed nisl</p>
  <p style="top:227px">Class aptent taciti sociosqu ad litora torquent per conubia nostra per inceptos hymenaeos Proin nulla arcu nonummy luctus dictum eget fermentum et lora</p>
</section>

<article class="card card-resources" style="left:117px">
  <h2>Resources Directory</h2>
  <div class="body">
    <svg class="icon" viewBox="0 0 74 72" fill="none" stroke="#2a9be0" stroke-width="2">
      <circle cx="30" cy="33" r="17"/><circle cx="30" cy="33" r="12"/>
      <line x1="30" y1="30" x2="30" y2="41"/><circle cx="30" cy="25" r="1.2" fill="#2a9be0"/>
      <path d="M16 22 L10 16 H3 M44 22 L50 16 H57 M16 44 L10 50 H3 M44 44 L50 50 H57 M13 33 H3 M47 33 H57 M30 16 V6 M30 50 V60"/>
      <circle cx="3" cy="16" r="2"/><circle cx="57" cy="16" r="2"/><circle cx="3" cy="50" r="2"/><circle cx="57" cy="50" r="2"/>
    </svg>
    Find what you need, when you need it.The KorvaNest website directory is your one-stop pit for anything involved in making money from home, marketing your business or finding a new opportunity. Our modern, community supported directory will help you keep upto todate with the lastest information in a sensible fashion
  </div>
</article>

<article class="card card-ads" style="left:358px">
  <h2>Advertising Benefits</h2>
  <div class="body">
    <svg class="icon" viewBox="0 0 74 72" fill="none" stroke="#2a9be0" stroke-width="2.4" stroke-linejoin="round">
      <path d="M4 22 H18 L58 6 V52 L18 38 H4 Z"/><path d="M18 22 V38"/>
      <path d="M14 38 L20 58 H28 L24 40"/><path d="M58 22 Q66 29 58 36"/>
    </svg>
    Everyone needs to advertise and we know just how to get your offer out to the right people. We have many methods including: Text ads, E-mail, Display, newsletter and even some old school methods available to make your next campaign a uccess. Advertise a website, a link text, full page circular or a small display ad and get results. Every advertiser recieves a dedicated account manager that will handle everything for You.
  </div>
</article>

<article class="card card-earn" style="left:596px">
  <h2>Earning with KorvaNest</h2>
  <div class="body">
    <svg class="icon" viewBox="0 0 74 72" fill="none" stroke="#2a9be0" stroke-width="2">
      <circle cx="32" cy="34" r="28" stroke-dasharray="4 4"/>
      <circle cx="32" cy="34" r="18"/><circle cx="32" cy="34" r="13" stroke-dasharray="2 2"/>
      <path d="M37 27 Q32 23 28 27 Q26 32 32 34 Q38 36 36 41 Q32 45 27 41 M32 21 V47"/>
    </svg>
    Join KorvaNest and start earning money. When you share KorvaNest and lock in an advertiser or premium listing, we reward you. Build a downline at any of our listed sites when you share KorvaNest with NO extra work. Its all done for you.We also offer a revenue share program for true supporters of our mission.
  </div>
</article>

<aside class="sidebar">
  <h2>Sponsor Listings</h2>
  <div class="sponsor" style="top:68px"><div class="sponsor-name">Brindlow</div><a href="#">Sponsor Tittle here</a></div>
  <div class="sponsor" style="top:152px"><div class="sponsor-name">Talvoro</div><a href="#">Sponsor Tittle here</a></div>
  <div class="sponsor" style="top:243px"><div class="sponsor-name">Merrant</div><a href="#">Sponsor Tittle here</a></div>
  <div class="ad ad-energy" role="img" aria-label="Clean energy advocacy banner advertisement"></div>
  <div class="ad ad-deli" role="img" aria-label="Local delicatessen banner advertisement"></div>
</aside>

<footer class="site-footer">
  <small>© 2017 Company Name&nbsp; All right reserved&nbsp; Term of Use</small>
  <div class="social" aria-label="Social links">
    <span></span><span></span><span></span><span></span>
  </div>
</footer>
</body>
</html>
```